Business Card for premium dental clinic

We are a premium dental clinic based in Brasov, Romania with more than 15 year on the market, providing quality dental treatment made by a team of more specialized dentists, working with modern equipment as a solution to beautiful and healthy teeth.

Our current logo for the clinic use 2 square with colors black and gold - dr Ternisu - studio, using family fonts Bodoni, Myriad Pro and Segoe Print.
Depending on the printing we used some gold CMYK background or gold foil picture background or a gold gradient.
We want a business card:
- eye catching business card
- distinguished business card
- premium design
- to keep the color scheme of black and gold
- to attract the customers to spent time reading the information
- modern concept

```html
<!DOCTYPE html>
<html lang="en">
<head>
<meta charset="utf-8">
<title>Lumina Dental – Business Card</title>
<link rel="stylesheet" href="https://fonts.googleapis.com/css2?family=Encode+Sans+Condensed:wght@400;500&family=Montserrat:wght@400;700&display=swap">
<style>
  :root {
    --backdrop: #2a2a2a;
    --card-black: #0c0c0c;
    --panel-black: #000000;
    --gold: #e7c23a;
    --gold-light: #f6dc6a;
    --gold-deep: #b8860b;
    --white: #ffffff;
    --ink: #1a1a1a;
    --muted-line: #8a8a8a;
  }
  * { margin: 0; padding: 0; box-sizing: border-box; }
  html, body {
    width: 1200px; height: 900px; overflow: hidden;
    background: var(--backdrop);
  }
  .canvas { position: relative; width: 1200px; height: 900px; }

  .card {
    position: absolute;
    width: 600px; height: 343px;
    background: var(--card-black);
    box-shadow: 0 10px 30px rgba(0,0,0,.5);
  }
  .card--front { left: 70px; top: 70px; }
  .card--back { left: 530px; top: 487px; }

  /* Front */
  .front-frame {
    position: absolute; left: 88px; top: 64px;
    width: 424px; height: 204px;
    border: 2px solid var(--white);
    display: flex;
  }
  .front-frame__gold {
    width: 40%; height: 100%;
    background: radial-gradient(circle at 30% 35%, var(--gold-light), var(--gold) 45%, var(--gold-deep) 100%);
  }
  .front-frame__black {
    flex: 1; height: 100%;
    background: var(--panel-black);
    display: flex; align-items: center; justify-content: center; gap: 10px;
  }
  .doctor-label {
    position: absolute; left: 60px; top: 98px;
    width: 170px; height: 54px;
    background: var(--white);
    display: flex; align-items: center; justify-content: center;
    font-family: "Encode Sans Condensed", sans-serif;
    color: var(--ink);
  }
  .doctor-label__prefix { font-size: 20px; margin-right: 2px; align-self: flex-end; margin-bottom: 12px; }
  .doctor-label__name { font-size: 34px; }
  .brand-mark { width: 12px; height: 12px; background: var(--gold); }
  .brand-name {
    font-family: "Montserrat", sans-serif; font-weight: 400;
    color: var(--white); font-size: 24px; letter-spacing: .5px;
  }
  .front-web {
    position: absolute; left: 0; right: 0; top: 288px;
    text-align: center;
    font-family: "Montserrat", sans-serif; font-size: 15px;
    color: var(--white); letter-spacing: .5px;
  }
  .front-web__accent { color: var(--gold); }

  /* Back */
  .back-brand {
    position: absolute; left: 70px; top: 150px;
    display: flex; align-items: center; gap: 10px;
  }
  .back-brand .brand-name { font-size: 20px; }
  .back-divider {
    position: absolute; left: 290px; top: 95px;
    width: 1px; height: 160px; background: var(--muted-line);
  }
  .contact {
    position: absolute; left: 315px; top: 100px;
    font-family: "Montserrat", sans-serif; color: var(--white);
  }
  .contact__name { color: var(--gold); font-weight: 700; font-size: 22px; letter-spacing: .5px; margin-bottom: 10px; }
  .contact__list { list-style: none; }
  .contact__item { display: flex; align-items: center; gap: 12px; font-size: 14px; line-height: 27px; }
  .contact__icon { width: 15px; height: 15px; stroke: var(--gold); fill: none; stroke-width: 1.6; flex: none; }
</style>
</head>
<body>
<main class="canvas">

  <section class="card card--front" aria-label="Business card front">
    <div class="front-frame">
      <div class="front-frame__gold" role="img" aria-label="Gold foil texture background"></div>
      <div class="front-frame__black">
        <span class="brand-mark"></span>
        <span class="brand-name">lumina dental</span>
      </div>
    </div>
    <div class="doctor-label">
      <span class="doctor-label__prefix">dr.</span><span class="doctor-label__name">ternisu</span>
    </div>
    <p class="front-web">www.<span class="front-web__accent">luminadental</span>.com</p>
  </section>

  <section class="card card--back" aria-label="Business card back">
    <div class="back-brand">
      <span class="brand-mark"></span>
      <span class="brand-name">lumina dental</span>
    </div>
    <div class="back-divider"></div>
    <div class="contact">
      <p class="contact__name">dr.ternisu</p>
      <ul class="contact__list">
        <li class="contact__item">
          <svg class="contact__icon" viewBox="0 0 16 16"><path d="M3 2h3l1.5 3.5-2 1.2a8 8 0 0 0 3.8 3.8l1.2-2L14 10v3a1 1 0 0 1-1 1A11 11 0 0 1 2 3a1 1 0 0 1 1-1z"/></svg>
          +00 000 555 0140
        </li>
        <li class="contact__item">
          <svg class="contact__icon" viewBox="0 0 16 16"><rect x="4" y="1.5" width="8" height="13" rx="1.5"/><line x1="7" y1="12" x2="9" y2="12"/></svg>
          +00 000 555 0140
        </li>
        <li class="contact__item">
          <svg class="contact__icon" viewBox="0 0 16 16"><rect x="1.5" y="3.5" width="13" height="9"/><path d="M1.5 3.5 8 9l6.5-5.5"/></svg>
          info@luminadental.com
        </li>
        <li class="contact__item">
          <svg class="contact__icon" viewBox="0 0 16 16"><circle cx="8" cy="8" r="6.5"/><ellipse cx="8" cy="8" rx="3" ry="6.5"/><line x1="1.5" y1="8" x2="14.5" y2="8"/></svg>
          www.luminadental.com
        </li>
      </ul>
    </div>
  </section>

</main>
</body>
</html>
```